Body Wash & Shampoo Label Design

Hello everyone,

I need a new logo/label design for a sister line of products to our main line. The Brand name is Velmora Trailside.

Here’s some insight to provide some inspiration. This brand will be social media based and will focus on adventure, travel, hiking, camping, and all other outdoors activities. Target market is outdoorsman – women. We will also be allocating a percentage of sales to various conservation efforts which we are narrowing down as we speak.

I’m not exactly sure what we are looking for in a logo/label designs so we are open to ideas and promote creativity. That said, we are looking for a simple and clean design that also speaks to our target market and would like the logo & label to be done at the same time so they compliment each other and fit well together.

Please incorporate an accent color somewhere in the design so new fragrances can be added down the line. This label will be going on a 16 fl oz cylindrical bottle with a toggle cap.

Label Details:

Width: 7.4 in
Height: 5.5 in
Distance from center of front to center of back: 3.7 in

Front (left):
- Logo
- Product Name: Driftwell Shampoo & Body Cleanser
- Highlights:
o No Rinse Nourishing Formula
o Sooths & Conditions
o Non-Sensitizing
o Non-Allergenic
- 16 Fl. Oz.

Back (right):

Tagline: More Cleanse, Less Hassle

Directions: Moisten wash cloth with Driftwell Shampoo & body cleanser. Use wash cloth to gently cleanse desired area. Pat dry if necessary. When shampooing, use was cloth to gently massage hair and scalp. Let air dry.

Warning: For external use only. Rinse eyes with water if contact should occur. Discontinue use in the case of local irritation. Contact physician if irritation persists for extended period of time.

Ingredients: Water, Disodium Cocoamphodiactate, Sodium C14-16 Olefine Sulfonate, ppg-2 hydroxyethyl Cocamide, Styrene/Acrylates Copolymer, Solvarin IV, Acrylates/C10-30 Alkyl Acrylate Crosspolymer, Fragrance, Aloe Barbadeniss Leaf Juice

Made in USA (either logo or words)

Address:
Quillan Products
214 Ashcombe Ln
Dover, NJ 07899

Barcode is also attached below. Looking forward to seeing your designs and thanks for the help! Let me know if you have any questions.

- Merle

Target Market(s)

Outdoorsman/women

Logo Text

Velmora Trailside

Colors

Designer to choose colors to be used in the design.

```html
<!DOCTYPE html>
<html lang="en">
<head>
<meta charset="utf-8">
<title>Velmora Trailside – Driftwell Shampoo &amp; Body Cleanser Labels</title>
<link rel="stylesheet" href="https://fonts.googleapis.com/css2?family=Oswald:wght@300;400&family=Montserrat:wght@500;600&display=swap">
<style>
  :root {
    --backdrop: #e4e4e4;
    --label: #ffffff;
    --glacier-deep: #1f5f93;
    --glacier-accent: #3a9fd8;
    --ember-deep: #8e1f1f;
    --ember-accent: #e4582a;
  }
  * { margin: 0; padding: 0; box-sizing: border-box; }
  html, body {
    width: 1200px;
    height: 803px;
    overflow: hidden;
    background: var(--backdrop);
  }
  .canvas {
    position: relative;
    width: 1200px;
    height: 803px;
  }
  .label {
    position: absolute;
    top: 230px;
    width: 250px;
    height: 470px;
    background: var(--label);
    border-radius: 6px;
    text-align: center;
  }
  .label--glacier { left: 360px; --deep: var(--glacier-deep); --accent: var(--glacier-accent); }
  .label--ember   { left: 600px; --deep: var(--ember-deep);   --accent: var(--ember-accent); }

  .brand {
    position: absolute;
    top: 80px;
    left: 0;
    right: 0;
    display: flex;
    flex-direction: column;
    align-items: center;
    color: var(--deep);
    font-family: "Oswald", sans-serif;
    font-weight: 400;
    line-height: 1;
  }
  .brand__dot {
    width: 22px;
    height: 22px;
    border-radius: 50%;
    background: var(--deep);
    margin-bottom: 8px;
  }
  .brand__name {
    font-size: 36px;
    letter-spacing: 0.5px;
    text-transform: uppercase;
  }
  .brand__name--sub {
    font-size: 17px;
    letter-spacing: 4px;
    margin-top: 4px;
  }

  .product-name {
    position: absolute;
    top: 226px;
    left: 0;
    right: 0;
    color: var(--deep);
    font-family: "Oswald", sans-serif;
    font-weight: 300;
    font-size: 16px;
    line-height: 22px;
    text-transform: uppercase;
  }

  .highlights {
    position: absolute;
    top: 342px;
    left: 0;
    right: 0;
    list-style: none;
    color: var(--deep);
    font-family: "Montserrat", sans-serif;
    font-weight: 600;
    font-size: 7px;
    line-height: 9px;
    text-transform: uppercase;
  }
  .highlights li::before { content: "• "; }

  .volume {
    position: absolute;
    top: 412px;
    left: 0;
    right: 0;
    color: var(--accent);
    font-family: "Montserrat", sans-serif;
    font-weight: 600;
    font-size: 12px;
    letter-spacing: 0.5px;
    word-spacing: 2px;
  }
  .volume__mark {
    font-size: 17px;
    padding: 0 4px;
  }
</style>
</head>
<body>
  <main class="canvas">

    <section class="label label--glacier" aria-label="Blue colourway front label">
      <div class="brand">
        <span class="brand__dot"></span>
        <span class="brand__name">Velmora</span>
        <span class="brand__name brand__name--sub">Trailside</span>
      </div>
      <h1 class="product-name">Driftwell Shampoo<br>&amp; Body Cleanser</h1>
      <ul class="highlights">
        <li>No Rinse Nourishing Formula</li>
        <li>Sooths &amp; Conditions</li>
        <li>Non-Sensitizing</li>
        <li>Non-Allergenic</li>
      </ul>
      <p class="volume">473 ML <span class="volume__mark">℮</span> 16 FL OZ</p>
    </section>

    <section class="label label--ember" aria-label="Red colourway front label">
      <div class="brand">
        <span class="brand__dot"></span>
        <span class="brand__name">Velmora</span>
        <span class="brand__name brand__name--sub">Trailside</span>
      </div>
      <h1 class="product-name">Driftwell Shampoo<br>&amp; Body Cleanser</h1>
      <ul class="highlights">
        <li>No Rinse Nourishing Formula</li>
        <li>Sooths &amp; Conditions</li>
        <li>Non-Sensitizing</li>
        <li>Non-Allergenic</li>
      </ul>
      <p class="volume">473 ML <span class="volume__mark">℮</span> 16 FL OZ</p>
    </section>

  </main>
</body>
</html>
```